Web Design Project - Shipping Industry

Goals and Objectives
The objective of the new website is to create a more modern look and feel. The site will also allow for a more effective means of communicating with members while providing the public with information and developments in the local, regional and international shipping industry.
Scope
The website will highlight the history of the organisation inclusive of text and photographs. It will take visitors through the years from beginning to present. Information on the history of the shipping industry will also be included.
It will feature current articles on the organisation, its members and stakeholders in the shipping industry. Member information as well as pertinent details regarding the organisation’s subsidiaries will be documented for the website.
Information as it relates to shipping statistics, case studies, laws and regulations, international treaties and trade documents, shipping terms, careers in shipping, job opportunities, training opportunities, information for shippers including port listing and trade lanes will be main features of the content for the website.
The Association’s community involvement, industry calendar events and related links relevant industry members will also be featured.
Target Market
• The General Public;
• Members of the organization;
• Shipping Industry Stakeholders (local, regional and international);
• Tertiary students conducting research.
• Potential employees
• Potential Business Partners
Best Practice Bench Marketing
The following websites are being looked at:
• Korvel Quayworks - http://www.korvelquayworks.example/ (preferred look)
• Tessaly Maritime Association - http://www.tma-freight.example/ (like image transition on main page)
• Drovna - http://www.drovna.example (professional look)
• PLW - http://www.pelworth.example (preferred color: blue in logo)
• Quillo - http://www.quillo.example/electronics/tv-video-audio/ (preferred look for links page: image + short text below + visit site link)
Expected Result
• 3 - 5 pages which must include: [1] main page [2] standard page [3] links page

```html
<!DOCTYPE html>
<html lang="en">
<head>
<meta charset="utf-8">
<title>Portavel PCS – Home</title>
<link href="https://fonts.googleapis.com/css2?family=Arimo:wght@400;700&display=swap" rel="stylesheet">
<style>
:root{
  --page-blue:#1f4b7d;
  --panel:#ffffff;
  --ink:#333333;
  --muted:#555555;
  --brand:#2a2461;
  --nav-top:#f0f27e;
  --nav-bottom:#d3e12c;
  --nav-line:#b9c52a;
  --link-red:#c8001e;
  --foot-text:#ffffff;
  --sky:#b9cde0;
  --sea:#5e7f95;
  --hull:#2c3440;
}
*{box-sizing:border-box;margin:0;padding:0}
html,body{width:1068px;height:1200px;overflow:hidden}
body{background:var(--page-blue);font-family:"Arimo",Arial,sans-serif;color:var(--ink);position:relative}
.site-panel{position:absolute;left:48px;top:28px;width:980px;height:1025px;background:var(--panel);
  background-image:linear-gradient(#f1f1f1,#fff 120px);box-shadow:0 0 0 2px #c9ced6}
.brand-name{position:absolute;left:32px;top:42px;font-size:31px;letter-spacing:6px;color:var(--brand);font-weight:400}
.world-map{position:absolute;left:609px;top:36px;width:92px;height:60px;border-radius:30px;
  background:radial-gradient(ellipse,#cfe3cc,rgba(255,255,255,0) 70%)}
.search{position:absolute;left:716px;top:53px;display:flex}
.search-field{width:196px;height:24px;border:1px solid #c8c8c8;background:#fff;box-shadow:inset 1px 2px 3px #ddd}
.search-button{width:52px;height:24px;background:linear-gradient(#444,#111);color:#fff;font-size:12px;line-height:24px;text-align:center}
.main-nav{position:absolute;left:13px;top:118px;width:954px;height:43px;
  background:linear-gradient(var(--nav-top),var(--nav-bottom));display:flex;padding-left:32px}
.main-nav a{display:block;height:43px;line-height:43px;font-size:14px;color:#333;text-decoration:none;
  text-align:center;border-right:1px solid var(--nav-line)}
.main-nav a.is-active{background:linear-gradient(#fff,#d8d8d8)}
.main-nav a:last-child{border-right:none}
.hero{position:absolute;left:39px;top:198px;width:910px;height:352px;background:#fff;
  border:1px solid #e6e6e6;box-shadow:0 6px 12px rgba(0,0,0,.12)}
.hero-image{position:absolute;left:15px;top:17px;width:880px;height:320px;
  background:linear-gradient(#c9d9ea 0%,#dfe8f1 40%,#6f7883 62%,#2c3440 88%,#8b8f86 100%);border:1px solid #a8b8c8}
.hero-caption{position:absolute;left:0;bottom:0;width:100%;height:40px;background:rgba(60,60,60,.72);
  color:#fff;font-size:13.5px;line-height:40px;padding-left:22px}
.slider-dots{position:absolute;left:473px;top:566px;display:flex;gap:5px}
.slider-dots span{width:11px;height:11px;border-radius:50%;background:#7d7d7d;box-shadow:inset 0 -1px 2px #444}
.slider-dots span.is-current{background:#e6ec4a;box-shadow:inset 0 -1px 2px #9a9a20}
.feature{position:absolute;top:602px;width:260px}
.feature h2{font-size:13.5px;font-weight:400;color:#333;letter-spacing:.3px}
.feature-image{margin-top:10px;width:250px;height:141px;border:3px solid #fff;box-shadow:0 0 3px #bbb}
.feature p{margin:15px 0 0 6px;font-size:11px;line-height:18.5px;color:var(--muted);width:230px}
.feature .more{display:block;margin:9px 0 0 6px;font-size:11px;color:var(--link-red);text-decoration:none}
.about{position:absolute;left:42px;top:900px;width:890px}
.about h2{display:inline-block;font-size:19px;font-weight:400;color:#444;padding:0 0 6px 4px;
  border-bottom:1px dotted #666;width:240px}
.about p{margin-top:14px;font-size:12px;line-height:26px;color:var(--muted)}
.footer{position:absolute;left:0;top:1053px;width:1068px;height:147px;color:var(--foot-text)}
.login h3{position:absolute;left:63px;top:18px;font-size:13px;font-weight:400}
.login-field{position:absolute;left:64px;width:144px;height:21px;background:#fff;color:#666;font-size:11px;line-height:21px;padding-left:8px}
.login-button{position:absolute;left:132px;top:107px;width:75px;height:27px;border-radius:4px;
  background:linear-gradient(#f4f58c,#d4df39);border:1px solid #b0b830;color:#222;font-size:13px;line-height:25px;text-align:center}
.footer-nav{position:absolute;left:272px;top:44px;font-size:11px;letter-spacing:.2px}
.footer-nav a{color:#fff;text-decoration:none}
.footer-nav .sep{margin:0 9px}
.copyright{position:absolute;left:0;width:1068px;top:83px;text-align:center;font-size:11px;padding-left:62px}
.social{position:absolute;top:39px;width:24px;height:24px;border-radius:3px}
</style>
</head>
<body>
<div class="site-panel">
  <div class="brand-name">PORTAVEL</div>
  <div class="world-map" role="img" aria-label="Faint dotted world map"></div>
  <div class="search"><div class="search-field"></div><div class="search-button">SEARCH</div></div>
  <nav class="main-nav">
    <a class="is-active" style="width:75px">HOME</a>
    <a style="width:102px">ABOUT US</a>
    <a style="width:139px">SUSTAINABILITY</a>
    <a style="width:73px">NEWS</a>
    <a style="width:97px">CAREERS</a>
    <a style="width:73px">LINKS</a>
    <a style="width:124px">CONTACT US</a>
  </nav>
  <div class="hero">
    <div class="hero-image" role="img" aria-label="Container ship loaded with stacked containers at sea">
      <div class="hero-caption">Nunc varius facilisis eros. Sed erat. In in velit quis arcu ornare laoreet. Curabitur adipiscing luctus massa.Integer ut purus ac augue commodo</div>
    </div>
  </div>
  <div class="slider-dots"><span></span><span></span><span class="is-current"></span><span></span><span></span></div>

  <div class="feature" style="left:42px">
    <h2>LIFTING GLOBAL TRADE</h2>
    <div class="feature-image" role="img" aria-label="Loaded container ship in harbour" style="background:linear-gradient(#c8cfd4 0%,#d6dbde 35%,#5b6a78 55%,#2f3e55 68%,#9aa59e 100%)"></div>
    <p>Nunc varius facilisis eros. Sed erat. In in velit quis arcu ornare laoreet. Curabitur adipiscing luctus massa.Integer ut purus ac commodo</p>
    <a class="more">View More &gt;&gt;</a>
  </div>
  <div class="feature" style="left:349px">
    <h2>WE ARE PORTAVEL</h2>
    <div class="feature-image" role="img" aria-label="Container ship sailing on open sea" style="background:linear-gradient(#6c9ccc 0%,#9fc0de 35%,#7a6e66 55%,#2b3a4a 66%,#2d7a8c 100%)"></div>
    <p>Nunc varius facilisis eros. Sed erat. In in velit quis arcu ornare laoreet. Curabitur adipiscing luctus massa.Integer ut purus ac commodo</p>
    <a class="more">View More &gt;&gt;</a>
  </div>
  <div class="feature" style="left:669px">
    <h2>PORTAVEL SUPPLY SERVICE</h2>
    <div class="feature-image" role="img" aria-label="Container ship with cranes under grey sky" style="background:linear-gradient(#cfd0d0 0%,#c4c6c6 45%,#6a5e52 58%,#2a2f36 68%,#7f8584 100%)"></div>
    <p>Nunc varius facilisis eros. Sed erat. In in velit quis arcu ornare laoreet. Curabitur adipiscing luctus massa.Integer ut purus ac commodo</p>
    <a class="more">View More &gt;&gt;</a>
  </div>

  <section class="about">
    <h2>ABOUT PORTAVEL PCS</h2>
    <p>Nunc varius facilisis eros. Sed erat. In in velit quis arcu ornare laoreet. Curabitur adipiscing luctus massa.Integer ut purus ac augue commodo commodo. Nunc nec mi eu justo tempor consectetuer. Etiam vitae nisl. In dignissim lacus ut ante. Cras elit lectus, bibendum a, adipiscing vitae, commodo et, dui.</p>
  </section>
</div>

<footer class="footer">
  <div class="login">
    <h3>MEMBER LOGIN</h3>
    <div class="login-field" style="top:46px">User ID</div>
    <div class="login-field" style="top:78px">Password</div>
    <div class="login-button">LOGIN</div>
  </div>
  <div class="footer-nav">
    <a>HOME</a><span class="sep">|</span><a>ABOUT US</a><span class="sep">|</span><a>SUSTAINABILITY</a><span class="sep">|</span><a>NEWS</a><span class="sep">|</span><a>CAREERS</a><span class="sep">|</span><a>LINKS</a><span class="sep">|</span><a>CONTACT US</a>
  </div>
  <div class="copyright">© 2012 Portavel PCS, All Rights Reserved</div>
  <div class="social" style="left:845px;background:#3b5a96"></div>
  <div class="social" style="left:886px;background:#4ab3e0"></div>
  <div class="social" style="left:927px;background:#ef6c24"></div>
  <div class="social" style="left:968px;background:#2a6fa6"></div>
  <div class="social" style="left:1010px;background:#e8e8e8"></div>
</footer>
</body>
</html>
```